Life Coaching and Personal Development Business. Needs Business Card with Logo

We are a Life Coaching and Personal Development Business based in Melbourne, Victoria. We specialise in assisting Individuals who find themselves at cross roads due to career, relationships or just life experiences that are preventing them from having extraordinary lives in happiness, finance or relationships or just being disconnected from a sense of purpose. Our motto is "we help you get there".

Reason: I am awaiting final concepts from a couple of designers

Reason: Deadline passed so now would like to see more options.

Target Market(s)

Individuals who want to move through the cross roads and who are aware that they require help to do so. They are seeking happy, for filing lives through all aspects career, relationships, family and finance

Industry/Entity Type

Finance

Font styles to use
Script

Requirements
Must have
• logo which is representative of moving forward
Business Name: RD Maple Harbour
ABN: 5038617294

I do not have a preference with colour but I do not want red orange or green

Should not have
• The card must not be to busy.

```html
<!DOCTYPE html>
<html lang="en">
<head>
<meta charset="utf-8">
<title>RD Maple Harbour – Business Card</title>
<link rel="stylesheet" href="https://fonts.googleapis.com/css2?family=Inter:wght@400;700&display=swap">
<style>
  :root {
    --teal: #0596b3;
    --teal-soft: #5cc1d5;
    --ink: #1a1a1a;
    --paper: #ffffff;
    --edge: #9fd6e3;
    --bevel: #e6e6e6;
  }
  html, body {
    margin: 0;
    padding: 0;
    width: 934px;
    height: 1200px;
    overflow: hidden;
    background: var(--paper);
    font-family: "Inter", Helvetica, Arial, sans-serif;
  }
  .sheet { position: relative; width: 934px; height: 1200px; }

  .card { position: absolute; left: 101px; width: 732px; height: 462px; box-sizing: border-box; }

  /* Front */
  .card-front { top: 86px; border: 1px solid var(--edge); background: var(--paper); }
  .brand-name {
    position: absolute; left: 0; right: 0; top: 186px;
    text-align: center; color: var(--teal);
    font-size: 38px; font-weight: 700; letter-spacing: -0.5px; margin: 0;
  }
  .holder-name {
    position: absolute; left: 0; right: 0; top: 292px;
    text-align: center; color: var(--ink);
    font-size: 20px; font-weight: 400; letter-spacing: -0.2px; margin: 0;
  }
  .holder-phone {
    position: absolute; left: 0; right: 0; top: 321px;
    text-align: center; color: var(--ink); font-size: 20px; margin: 0;
  }
  .holder-phone svg { vertical-align: -2px; margin-right: 5px; }

  /* Back */
  .card-back { top: 643px; background: var(--teal); overflow: hidden; }
  .motto {
    position: absolute; left: 0; right: 0; top: 96px; margin: 0;
    text-align: center; color: var(--teal-soft);
    font-size: 62px; font-weight: 700; line-height: 68px; letter-spacing: -2.5px;
  }
  .tab-left { position: absolute; left: 0; top: 288px; width: 36px; height: 63px; background: var(--paper); }
  .tab-mid { position: absolute; left: 425px; top: 288px; width: 36px; height: 63px; background: var(--paper); }
  .tab-bevel { position: absolute; left: 460px; top: 265px; }
  .band-right { position: absolute; left: 481px; top: 265px; right: 0; height: 63px; background: var(--paper); }
  .contact {
    position: absolute; left: 36px; width: 384px; top: 293px;
    text-align: center; color: var(--paper); font-size: 20px; line-height: 30px;
    margin: 0; padding: 0; list-style: none;
  }
  .contact svg { vertical-align: -2px; margin-right: 8px; }
</style>
</head>
<body>
<main class="sheet">
  <section class="card card-front" aria-label="Card front">
    <p class="brand-name">RD Maple Harbour</p>
    <p class="holder-name">CLARA WENTON</p>
    <p class="holder-phone">
      <svg width="10" height="16" viewBox="0 0 10 16" aria-hidden="true">
        <rect x="1" y="1" width="8" height="14" rx="1.5" fill="none" stroke="var(--teal)" stroke-width="1.5"/>
        <line x1="4" y1="12.5" x2="6" y2="12.5" stroke="var(--teal)" stroke-width="1.2"/>
      </svg>04183 52716
    </p>
  </section>

  <section class="card card-back" aria-label="Card back">
    <h2 class="motto">We help you<br>get there</h2>
    <div class="tab-left"></div>
    <ul class="contact">
      <li>
        <svg width="16" height="12" viewBox="0 0 16 12" aria-hidden="true">
          <rect x="0.75" y="0.75" width="14.5" height="10.5" fill="none" stroke="var(--paper)" stroke-width="1.3"/>
          <polyline points="1,1 8,7 15,1" fill="none" stroke="var(--paper)" stroke-width="1.3"/>
        </svg>clara@rdmapleharbour.com.au
      </li>
      <li>
        <svg width="11" height="16" viewBox="0 0 11 16" aria-hidden="true">
          <path d="M5.5 0.5a5 5 0 0 1 5 5c0 3.6-5 10-5 10s-5-6.4-5-10a5 5 0 0 1 5-5z" fill="var(--paper)"/>
          <circle cx="5.5" cy="5.5" r="2" fill="var(--teal)"/>
        </svg>P.O. Box 4129, Seaview VIC 3188
      </li>
    </ul>
    <div class="tab-mid"></div>
    <svg class="tab-bevel" width="22" height="86" viewBox="0 0 22 86" aria-hidden="true">
      <polygon points="0,23 22,0 22,63 0,86" fill="var(--bevel)"/>
    </svg>
    <div class="band-right"></div>
  </section>
</main>
</body>
</html>
```